Website for new crypto research organization

See brief (attached). This is a pretty basic website with only a handful of pages + ability to collect email addresses.

```html
<!DOCTYPE html>
<html lang="en">
<head>
<meta charset="utf-8">
<title>Tidewater Research</title>
<link href="https://fonts.googleapis.com/css2?family=Lato:wght@400;700&family=Roboto:wght@500;700&display=swap" rel="stylesheet">
<style>
:root{
  --teal:#1aa8a3;
  --teal-light:#1cbdb5;
  --teal-dark:#12918d;
  --ink:#1f1f1f;
  --text:#333;
  --muted:#555;
  --brick:#8c2a34;
  --brick-dark:#5e1a25;
  --white:#fff;
  --black:#000;
}
*{margin:0;padding:0;box-sizing:border-box}
html,body{width:1200px;height:2601px;overflow:hidden;background:var(--white)}
body{position:relative;font-family:'Lato',sans-serif;color:var(--text)}
.abs{position:absolute}
h2,h3,h4,.btn,.nav a,.tag,.date{font-family:'Roboto',sans-serif}

/* header */
.brand{left:133px;top:12px;width:124px;height:68px;border:2px solid var(--teal);display:flex;align-items:center;justify-content:center;text-align:center;color:var(--teal);font-family:'Roboto',sans-serif;font-weight:700;font-size:15px;line-height:1.1}
.nav{top:36px;left:584px;display:flex;gap:35px}
.nav a{color:#222;text-decoration:none;font-size:13px;font-weight:500;letter-spacing:.2px}

/* hero */
.hero{left:12px;top:104px;width:1176px;height:556px;background:radial-gradient(ellipse at 50% 45%,var(--brick) 40%,var(--brick-dark) 85%,#2c4f63 100%);border-radius:18px;display:flex;flex-direction:column;align-items:center;justify-content:center;color:var(--white)}
.hero-name{font-family:'Roboto',sans-serif;font-weight:700;font-size:84px;letter-spacing:2px;line-height:1;margin-top:60px}
.hero-sub{font-family:'Roboto',sans-serif;font-weight:700;font-size:46px;letter-spacing:20px;margin-top:12px}
.dots{top:557px;left:577px;display:flex;gap:4px}
.dots span{width:9px;height:9px;border-radius:50%;background:var(--white)}
.dots span:first-child{background:var(--teal-light)}

/* section titles */
.title{left:0;width:1200px;text-align:center;font-size:31px;font-weight:700;color:var(--ink)}
.rule{left:580px;width:40px;height:4px;background:var(--teal)}

.about-text{left:138px;top:798px;width:924px;text-align:justify;text-align-last:center;font-size:14px;line-height:24px;color:var(--text)}
.btn{display:flex;align-items:center;justify-content:center;font-size:15px;font-weight:500;text-decoration:none}
.btn-learn{left:510px;top:970px;width:182px;height:47px;background:linear-gradient(var(--teal-light),var(--teal-dark));color:var(--white)}

/* research band */
.band{left:0;top:1090px;width:1200px;height:710px}
.card{width:308px;height:266px;padding:20px 12px;border:2px solid var(--white);color:var(--white)}
.card.solid{background:var(--white);color:var(--text);box-shadow:0 2px 10px rgba(0,0,0,.2)}
.date{font-size:12px;font-weight:700}
.tags{display:flex;gap:6px;margin:12px 0 14px}
.tag{width:91px;height:31px;border:2px solid var(--white);border-radius:16px;display:flex;align-items:center;justify-content:center;font-size:11.5px;font-weight:500}
.card.solid .tag{border-color:var(--teal);color:var(--teal)}
.card h3{font-size:18px;font-weight:700;line-height:24px;text-transform:uppercase}
.card.solid h3{color:var(--ink)}
.card.solid .date{color:var(--teal)}
.card p{font-size:12px;line-height:24px;margin-top:4px}
.card a{display:block;margin-top:8px;font-family:'Roboto',sans-serif;font-size:12px;font-weight:700;color:inherit}
.card.solid a{color:var(--teal)}
.btn-reports{left:478px;top:1606px;width:244px;height:48px;background:var(--white);color:var(--teal)}

/* news */
.news{width:304px;height:192px;border:1px solid #cfcfcf;padding:22px 17px;background:var(--white)}
.news.raised{box-shadow:0 3px 12px rgba(0,0,0,.18);border-color:transparent}
.news .kind{font-size:12px;color:var(--teal);font-weight:700}
.news h4{font-size:16px;font-weight:500;color:var(--ink);line-height:23px;margin-top:6px}
.news p{font-size:12.5px;line-height:23px;margin-top:9px;color:var(--muted)}

/* footer */
.footer{left:0;top:2190px;width:1200px;height:411px}
.foot-brand{left:131px;top:2355px;width:156px;height:88px;display:flex;align-items:center;justify-content:center;color:var(--white);font-family:'Roboto',sans-serif;font-weight:700;font-size:17px;text-align:center;line-height:1.2}
.fh{font-family:'Roboto',sans-serif;font-size:15px;font-weight:700;color:var(--white)}
.links{list-style:none;color:var(--white);font-size:14px}
.links li{height:28px;display:flex;align-items:center;gap:14px}
.contact-row{display:flex;gap:12px;color:var(--white);font-size:14px;line-height:28px}
.ico{flex:none;width:31px;height:31px;border-radius:50%;background:var(--teal);display:flex;align-items:center;justify-content:center}
.news-intro{color:var(--white);font-size:14px;line-height:28px}
.subscribe{display:flex;width:254px;height:40px}
.subscribe input{flex:1;border:0;padding:0 13px;font-family:'Lato',sans-serif;font-size:11px;color:#777}
.subscribe button{width:53px;border:0;background:var(--teal);display:flex;align-items:center;justify-content:center}
.socials{display:flex;gap:14px}
.socials span{width:30px;height:30px;border-radius:50%;background:var(--teal)}
.foot-rule{left:112px;top:2527px;width:963px;height:1px;background:#777}
.copy{left:0;width:1200px;top:2545px;text-align:center;color:var(--white);font-size:14px}
</style>
</head>
<body>

<div class="abs brand">TIDEWATER<br>RESEARCH</div>
<nav class="abs nav">
  <a href="#">HOME</a><a href="#">ABOUT</a><a href="#">RESEARCH</a><a href="#">NEWS</a><a href="#">CAREERS</a><a href="#">CONTACT</a>
</nav>

<section class="abs hero" role="img" aria-label="Painted brick wall in deep red with blue and teal splashes, framed by rough brush edges">
  <div class="hero-name">TIDEWATER</div>
  <div class="hero-sub">RESEARCH</div>
</section>
<div class="abs dots"><span></span><span></span><span></span><span></span></div>

<h2 class="abs title" style="top:722px">ABOUT TIDEWATER RESEARCH</h2>
<div class="abs rule" style="top:773px"></div>
<p class="abs about-text">Sed ut perspiciatis unde omnis iste natus error sit voluptatem accusantium doloremque laudantium, totam rem aperiam, eaque ipsa quae ab illo inventore veritatis et quasi architecto beatae vitae dicta sunt explicabo. Nemo enim ipsam voluptatem quia voluptas sit aspernatur aut odit aut fugit, sed quia consequuntur magni dolores eos qui ratione voluptatem sequi nesciunt. Neque porro quisquam est, qui dolorem ipsum quia dolor sit amet, consectetur, adipisci velit, sed quia non numquam eius modi tempora incidunt ut labore et dolore magnam aliquam quaerat voluptatem. Ut enim ad minima veniam, quis nostrum exercitationem ullam corporis suscipit laboriosam, nisi ut aliquid ex ea commodi consequatur? Quis autem vel eum iure reprehenderit qui in ea voluptate velit esse quam nihil molestiae consequatur, vel illum qui dolorem eum fugiat quo voluptas nulla</p>
<a class="abs btn btn-learn" href="#">LEARN MORE</a>

<svg class="abs band" viewBox="0 0 1200 710" preserveAspectRatio="none" aria-hidden="true">
  <defs>
    <linearGradient id="bandFill" x1="0" y1="0" x2="1" y2="1">
      <stop offset="0" stop-color="#14a39e"/><stop offset=".5" stop-color="#1bbab2"/><stop offset="1" stop-color="#16a49f"/>
    </linearGradient>
  </defs>
  <path fill="url(#bandFill)" d="M0 70 L40 55 L70 80 L110 50 L150 72 L200 48 L240 66 L300 42 L350 60 L400 38 L460 55 L520 30 L580 52 L640 28 L700 45 L760 25 L820 42 L880 20 L940 38 L1000 22 L1060 35 L1120 18 L1160 10 L1200 0 L1200 600 L1160 612 L1120 590 L1080 615 L1040 585 L990 620 L940 598 L880 628 L820 605 L760 632 L700 612 L640 640 L580 618 L520 645 L460 625 L400 652 L340 630 L280 660 L220 640 L160 668 L100 650 L50 680 L0 690 Z"/>
</svg>

<h2 class="abs title" style="top:1222px;color:var(--white)">OUR RESEARCH</h2>
<div class="abs rule" style="top:1273px;background:var(--white)"></div>

<article class="abs card" style="left:125px;top:1305px">
  <div class="date">09 JAN 2022</div>
  <div class="tags"><span class="tag">EIUSMOD</span><span class="tag">EIUSMOD</span><span class="tag">EIUSMOD</span></div>
  <h3>Lorem ipsum dolor sit amet consectetur adipis.</h3>
  <p>Lorem ipsum dolor sit amet, consectetur adip iscing elit, sed do eiusmod tempor incididunt ut labore et dolore magna aliqua.</p>
  <a href="#">LEARN MORE</a>
</article>
<article class="abs card solid" style="left:447px;top:1305px">
  <div class="date">09 JAN 2022</div>
  <div class="tags"><span class="tag">EIUSMOD</span><span class="tag">EIUSMOD</span><span class="tag">EIUSMOD</span></div>
  <h3>Lorem ipsum dolor sit amet consectetur adipis.</h3>
  <p>Lorem ipsum dolor sit amet, consectetur adip iscing elit, sed do eiusmod tempor incididunt ut labore et dolore magna aliqua.</p>
  <a href="#">LEARN MORE</a>
</article>
<article class="abs card" style="left:768px;top:1305px">
  <div class="date">09 JAN 2022</div>
  <div class="tags"><span class="tag">EIUSMOD</span><span class="tag">EIUSMOD</span><span class="tag">EIUSMOD</span></div>
  <h3>Lorem ipsum dolor sit amet consectetur adipis.</h3>
  <p>Lorem ipsum dolor sit amet, consectetur adip iscing elit, sed do eiusmod tempor incididunt ut labore et dolore magna aliqua.</p>
  <a href="#">LEARN MORE</a>
</article>
<a class="abs btn btn-reports" href="#">RECENT RESEARCH REPORTS</a>

<h2 class="abs title" style="top:1832px">OUR LATEST NEWS</h2>
<div class="abs rule" style="top:1883px"></div>

<article class="abs news" style="left:131px;top:1921px">
  <div class="kind">ARTICLES</div>
  <h4>Lorem ipsum dolor sit amet consect etur adipiscing elit sed do.</h4>
  <p>Lorem ipsum dolor sit amet, consectetur adipi scing elit, sed do eiusmod tempor incididunt ut labore et dolore magna aliqua.</p>
</article>
<article class="abs news raised" style="left:448px;top:1921px">
  <div class="kind">PODCASTS</div>
  <h4>Lorem ipsum dolor sit amet consect etur adipiscing elit sed do.</h4>
  <p>Lorem ipsum dolor sit amet, consectetur adipi scing elit, sed do eiusmod tempor incididunt ut labore et dolore magna aliqua.</p>
</article>
<article class="abs news" style="left:764px;top:1921px">
  <div class="kind">BLOG POSTS</div>
  <h4>Lorem ipsum dolor sit amet consect etur adipiscing elit sed do.</h4>
  <p>Lorem ipsum dolor sit amet, consectetur adipi scing elit, sed do eiusmod tempor incididunt ut labore et dolore magna aliqua.</p>
</article>

<svg class="abs footer" viewBox="0 0 1200 411" preserveAspectRatio="none" aria-hidden="true">
  <path fill="#000" d="M0 40 L50 30 L90 48 L140 25 L190 40 L240 22 L300 36 L360 15 L420 32 L480 12 L540 28 L600 10 L660 24 L720 8 L780 22 L840 6 L900 18 L960 4 L1020 15 L1080 2 L1140 8 L1200 0 L1200 411 L0 411 Z"/>
</svg>

<div class="abs foot-brand">TIDEWATER<br>RESEARCH</div>

<div class="abs fh" style="left:370px;top:2312px">QUICK LINKS</div>
<ul class="abs links" style="left:370px;top:2338px">
  <li><span>»</span>Home</li><li><span>»</span>About</li><li><span>»</span>Research</li><li><span>»</span>News</li><li><span>»</span>Careers</li><li><span>»</span>Contact</li>
</ul>

<div class="abs fh" style="left:537px;top:2312px">CONTACT US</div>
<div class="abs contact-row" style="left:537px;top:2342px;width:240px">
  <span class="ico"><svg width="12" height="16" viewBox="0 0 12 16"><path fill="#fff" d="M6 0a6 6 0 0 0-6 6c0 4.5 6 10 6 10s6-5.5 6-10a6 6 0 0 0-6-6zm0 8.3A2.3 2.3 0 1 1 6 3.7a2.3 2.3 0 0 1 0 4.6z"/></svg></span>
  <span>123 Lorem ipsum dolor sit amet consectetur adipiscing elit.</span>
</div>
<div class="abs contact-row" style="left:537px;top:2414px">
  <span class="ico"><svg width="15" height="15" viewBox="0 0 16 16"><path fill="#fff" d="M3.6 1l2.3 3.2-1.4 1.6a9 9 0 0 0 5.7 5.7l1.6-1.4L15 12.4 13.6 15C6.8 15 1 9.2 1 2.4z"/></svg></span>
  <span>+1 888 8888 888</span>
</div>
<div class="abs contact-row" style="left:537px;top:2469px">
  <span class="ico"><svg width="15" height="11" viewBox="0 0 16 12"><path fill="#fff" d="M0 0h16v1.5L8 6.5 0 1.5zM0 3.5l8 5 8-5V12H0z"/></svg></span>
  <span>hello@tidewaterresearch.com</span>
</div>

<div class="abs fh" style="left:830px;top:2312px">SIGN UP FOR OUR NEWSLETTER</div>
<p class="abs news-intro" style="left:829px;top:2337px;width:240px">Lorem ipsum dolor sit amet, consectet ur adipiscing elit, sed do.</p>
<form class="abs subscribe" style="left:829px;top:2404px">
  <input type="email" placeholder="Enter The Email">
  <button type="button" aria-label="Subscribe"><svg width="16" height="16" viewBox="0 0 16 16"><path fill="#fff" d="M16 0L0 7l5 2 1 6 3-4 4 3z"/></svg></button>
</form>
<div class="abs socials" style="left:831px;top:2466px"><span></span><span></span><span></span><span></span></div>

<div class="abs foot-rule"></div>
<p class="abs copy">© Copyrights 2022 &nbsp;Tidewater Research &nbsp;| &nbsp;&nbsp;All Rights Reserved</p>

</body>
</html>
```